Residential building / Apartments for sale landing page

I need a website / landing page design for my latest development project - a residential building with 70+ apartments for sale. I need the design in layers in Photoshop/Illustrator/InDesign format with all the icons/shapes/maps/graphic assets in vector format (svg, ai, eps) as much as possible.

I prefer white website and please consider the performance/coding experience. We're not making something suitable only for a design contest with fancy parallax effects and confusing animations. We're trying to create usable and clean UI with good UX.

The website will be custom coded, i.e. I'm not using WordPress.

I know that the existing 3D photos are not good but for now you can use them or replace them with some stock photos. I'm going to create new 3D photos soon.

Real Estate Development

1 page

```html
<!DOCTYPE html>
<html lang="en">
<head>
<meta charset="utf-8">
<title>Pine Hollow – Apartments for Sale</title>
<link rel="stylesheet" href="https://fonts.googleapis.com/css2?family=Marcellus&family=Lato:wght@400;700;900&display=swap">
<style>
:root{
  --green:#7dc242;
  --green-dark:#5fa52a;
  --ink:#1f1b1b;
  --text:#333;
  --muted:#777;
  --white:#fff;
  --line:#d8d8d8;
}
*{box-sizing:border-box;margin:0;padding:0}
html,body{width:1200px;height:4566px;overflow:hidden}
body{position:relative;background:var(--white);font-family:'Lato',sans-serif;color:var(--text)}
.abs{position:absolute}
.btn{position:absolute;display:flex;align-items:center;justify-content:center;border-radius:28px;font-weight:900;color:var(--white);background:var(--green);font-size:17px;letter-spacing:.3px}
.btn-dark{background:var(--ink);color:var(--green)}
.section-title{position:absolute;left:0;width:1200px;text-align:center;font-family:'Marcellus',serif;font-size:38px;color:var(--ink);letter-spacing:.5px;font-weight:400}

/* hero */
.hero{position:absolute;left:0;top:0;width:1200px;height:815px;background:linear-gradient(180deg,#c9e7df 0%,#6f8f86 18%,#3e5a4b 45%,#2a3a30 100%)}
.brand{position:absolute;left:142px;top:34px;display:flex;align-items:center;gap:10px;font-weight:900;font-size:27px;color:var(--ink);letter-spacing:.5px}
.brand-mark{width:18px;height:18px;background:var(--green)}
.nav{position:absolute;top:62px;left:0;width:1200px;font-size:14px;font-weight:700;color:var(--ink)}
.nav span{position:absolute;transform:translateX(-50%);white-space:nowrap}
.lang{position:absolute;left:975px;top:10px;width:80px;height:28px;border:1px solid #ddd;background:rgba(255,255,255,.85);font-size:11px;display:flex;align-items:center;justify-content:center;gap:6px;font-weight:700}
.lang i{display:inline-block;width:16px;height:10px;background:#2c4a9a}
.hero-title{position:absolute;top:242px;left:0;width:1200px;text-align:center;font-family:'Marcellus',serif;font-weight:400;font-size:41px;line-height:51px;color:var(--white)}
.hero-price{position:absolute;top:420px;left:0;width:1200px;text-align:center;font-weight:900;font-size:29px;color:var(--white)}
.dots{position:absolute;top:627px;left:560px;display:flex;gap:9px}
.dots b{width:9px;height:9px;border-radius:50%;background:var(--white)}
.dots b.on{background:var(--green)}

/* presentation */
.pres-photo{position:absolute;left:0;top:830px;width:1200px;height:652px;background:linear-gradient(180deg,#fff 0%,#fff 22%,#dfe4e8 50%,#a9b3ba 100%)}
.pres-text{position:absolute;left:235px;top:970px;width:730px;text-align:center;font-size:13.5px;line-height:23.5px;color:#666}

/* benefits */
.benefits{position:absolute;left:0;top:1482px;width:1200px;height:782px;background:linear-gradient(180deg,#79be3b,#6fb52f)}
.benefits .section-title{color:var(--white);top:85px}
.benefit{position:absolute;width:300px}
.benefit .ico{position:absolute;left:0;top:0;width:92px;height:92px;border-radius:50%;border:3px solid var(--white);display:flex;align-items:center;justify-content:center}
.benefit h3{position:absolute;left:110px;top:0;font-size:19px;line-height:25px;color:var(--white);font-weight:700;width:190px}
.benefit p{position:absolute;left:110px;font-size:12.5px;line-height:20px;color:#eef8e4;width:170px}
.silhouette{position:absolute;left:0;top:620px;width:1200px;height:162px;background:linear-gradient(180deg,rgba(255,255,255,0),rgba(255,255,255,.9) 85%,#fff)}

/* features */
.card{position:absolute;top:2471px;width:287px;height:314px;border:2px solid #e0e0e0;background:var(--white);text-align:center}
.card svg{margin-top:42px}
.card h3{position:absolute;top:170px;left:0;width:100%;font-size:19px;font-weight:700;color:var(--ink)}
.card p{position:absolute;top:208px;left:35px;width:215px;font-size:12.5px;line-height:21px;color:#888}
.arrow{position:absolute;width:46px;height:46px;border-radius:50%;border:2px solid #aaa;background:var(--white);display:flex;align-items:center;justify-content:center}

/* location */
.map{position:absolute;left:0;top:2861px;width:1200px;height:487px;background:linear-gradient(100deg,#7fae7a 0%,#8fbf86 30%,#6d8fd6 55%,#5f86d8 100%)}
.loc-card{position:absolute;left:144px;top:2980px;width:358px;height:250px;background:var(--white);text-align:center}
.loc-card h2{font-family:'Marcellus',serif;font-weight:400;font-size:38px;color:var(--ink);margin-top:46px}
.loc-card p{font-size:12.5px;line-height:21px;color:#777;margin:20px 28px 0}

/* gallery */
.gal-sub{position:absolute;top:3505px;left:0;width:1200px;text-align:center;font-size:14px;color:#777}
.shot{position:absolute;top:3575px;width:287px;height:223px}
.shot span{position:absolute;left:24px;top:170px;font-size:15px;font-weight:700;color:var(--white)}
.shot .btn{left:175px;top:165px;width:85px;height:31px;font-size:15px;border-radius:16px}

/* contact */
.contact{position:absolute;left:0;top:3870px;width:1200px;height:696px}
.contact h2{position:absolute;top:210px;left:0;width:1200px;text-align:center;font-family:'Marcellus',serif;font-weight:400;font-size:38px;color:var(--green)}
.col-title{position:absolute;font-size:19px;font-weight:900;color:var(--white)}
.info{position:absolute;left:193px;display:flex;align-items:center;gap:16px;font-size:16px;line-height:24px;color:var(--white)}
.info .c{width:50px;height:50px;border-radius:50%;background:var(--green);flex:none;display:flex;align-items:center;justify-content:center}
.field{position:absolute;left:633px;width:372px;height:39px;background:var(--white);font-size:13px;color:#666;padding:12px 16px}
.send{position:absolute;left:633px;top:538px;width:110px;height:36px;background:var(--green);color:var(--white);font-weight:900;font-size:18px;display:flex;align-items:center;justify-content:center;letter-spacing:1px}
.copy{position:absolute;top:632px;left:0;width:1200px;text-align:center;font-size:12.5px;color:var(--white)}
</style>
</head>
<body>

<!-- hero -->
<header class="hero" role="img" aria-label="Residential buildings in front of a forested mountain"></header>
<svg class="abs" style="left:0;top:0" width="1200" height="830" viewBox="0 0 1200 830">
  <polygon points="0,558 600,815 1200,558 1200,830 0,830" fill="#fff"/>
  <polygon points="418,806 600,691 780,806 600,815" fill="#1f1b1b"/>
  <polyline points="0,558 600,815 1200,558" fill="none" stroke="#1f1b1b" stroke-width="8"/>
  <polyline points="0,548 600,803 1200,548" fill="none" stroke="#7dc242" stroke-width="8"/>
  <polyline points="418,806 600,691 780,806" fill="none" stroke="#7dc242" stroke-width="7"/>
</svg>
<div class="brand"><span class="brand-mark"></span>PINE HOLLOW</div>
<nav class="nav">
  <span style="left:533px">PINE HOLLOW</span>
  <span style="left:660px">THE PROJECT</span>
  <span style="left:793px">APARTMENTS</span>
  <span style="left:915px">LOCATION</span>
  <span style="left:1022px">GALLERY</span>
</nav>
<div class="lang"><i></i>EN ▾</div>
<h1 class="hero-title">SALE OF APARTMENTS DIRECTLY<br>FROM THE INVESTOR WITH<br>10% DISCOUNT</h1>
<div class="hero-price">Price from 000 EUR/m2</div>
<div class="btn" style="left:516px;top:500px;width:166px;height:54px;font-size:20px">BUY</div>
<div class="dots"><b></b><b></b><b class="on"></b><b></b><b></b></div>

<!-- project presentation -->
<div class="pres-photo" role="img" aria-label="White apartment blocks under a blue sky"></div>
<h2 class="section-title" style="top:896px">PROJECT PRESENTATION</h2>
<p class="pres-text">Lorem ipsum dolor sit amet, consectetur adipiscing elit, sed do eiusmod tempor incididunt ut labore et dolore magna aliqua. Quis ipsum suspendisse ultrices s commodo viverra maecenas accumsan lacus vel facilisis, rem ipsum dolor sit amet, consectetur adipiscing elit, sed do eiusmod tempor incididunt ut labore et dolore magna aliquis ipsum suspe ndisse ultrices s commodo viverra maecenas accumsan lacus vel facilisis.</p>
<div class="btn" style="left:517px;top:1100px;width:166px;height:53px">READ MORE</div>

<!-- benefits -->
<section class="benefits">
  <h2 class="section-title">OUR BENEFITS</h2>
  <div class="benefit" style="left:138px;top:204px">
    <div class="ico"><svg width="44" height="44" viewBox="0 0 44 44"><path d="M8 36 C10 16 24 8 38 8 C38 24 28 36 12 34 Z" fill="#fff"/><path d="M8 36 L28 18" stroke="#79be3b" stroke-width="2"/></svg></div>
    <h3>Green areas<br>and gardens</h3>
    <p style="top:56px">Lorem ipsum dolor sit ameconsectetur adipiscing</p>
  </div>
  <div class="benefit" style="left:461px;top:204px">
    <div class="ico"><svg width="56" height="56" viewBox="0 0 56 56"><circle cx="28" cy="28" r="24" fill="none" stroke="#fff" stroke-width="3"/><text x="28" y="38" text-anchor="middle" font-family="Lato,sans-serif" font-weight="700" font-size="28" fill="#fff">P</text></svg></div>
    <h3>Parking spaces</h3>
    <p style="top:32px">Lorem ipsum dolor sit ameconsectetur adipiscing eed do eiusmod tempo</p>
  </div>
  <div class="benefit" style="left:782px;top:204px">
    <div class="ico"><svg width="60" height="40" viewBox="0 0 60 40"><circle cx="14" cy="26" r="10" fill="none" stroke="#fff" stroke-width="3"/><circle cx="46" cy="26" r="10" fill="none" stroke="#fff" stroke-width="3"/><path d="M14 26 L24 12 L40 12 L46 26 M24 12 L30 26 L40 12 M20 8 h8" fill="none" stroke="#fff" stroke-width="3"/></svg></div>
    <h3>Bicycle parking</h3>
    <p style="top:32px">Lorem ipsum dolor sit ameconsectetur adipiscing eed do eiusmod tempo</p>
  </div>
  <div class="benefit" style="left:138px;top:380px">
    <div class="ico"><svg width="40" height="48" viewBox="0 0 40 48"><polygon points="20,2 30,16 25,16 34,28 27,28 38,40 2,40 13,28 6,28 15,16 10,16" fill="#fff"/><rect x="17" y="40" width="6" height="7" fill="#fff"/></svg></div>
    <h3>Outside workout<br>area</h3>
    <p style="top:56px">Lorem ipsum dolor sit ameconsectetur adipiscing</p>
  </div>
  <div class="benefit" style="left:461px;top:380px">
    <div class="ico"><svg width="44" height="44" viewBox="0 0 44 44"><circle cx="22" cy="22" r="14" fill="#fff"/><g fill="#fff"><circle cx="22" cy="5" r="4"/><circle cx="22" cy="39" r="4"/><circle cx="5" cy="22" r="4"/><circle cx="39" cy="22" r="4"/><circle cx="10" cy="10" r="4"/><circle cx="34" cy="34" r="4"/><circle cx="34" cy="10" r="4"/><circle cx="10" cy="34" r="4"/></g></svg></div>
    <h3>NFC controlled<br>access</h3>
    <p style="top:56px">Lorem ipsum dolor sit ameconsectetur adipiscing</p>
  </div>
  <div class="benefit" style="left:782px;top:380px">
    <div class="ico"><svg width="50" height="50" viewBox="0 0 50 50"><circle cx="25" cy="25" r="20" fill="none" stroke="#fff" stroke-width="2" stroke-dasharray="3 4"/><circle cx="25" cy="15" r="4" fill="#fff"/><path d="M15 38 h20 M25 20 v10 M16 24 L25 28 L34 24 M18 36 l7 -6 l7 6" fill="none" stroke="#fff" stroke-width="3"/></svg></div>
    <h3>Outdoor Yoga area</h3>
    <p style="top:32px">Lorem ipsum dolor sit ameconsectetur adipiscing eed do eiusmod tempo</p>
  </div>
  <div class="btn btn-dark" style="left:517px;top:553px;width:166px;height:53px">VIEW MORE</div>
  <div class="silhouette" role="img" aria-label="White silhouettes of pine trees and a house"></div>
</section>

<!-- construction features -->
<h2 class="section-title" style="top:2364px">CONSTRUCTION FEATURES</h2>
<div class="arrow" style="left:76px;top:2609px"><svg width="12" height="18" viewBox="0 0 12 18"><path d="M9 2 L3 9 L9 16" fill="none" stroke="#555" stroke-width="2"/></svg></div>
<div class="card" style="left:144px">
  <svg width="70" height="80" viewBox="0 0 70 80"><rect x="4" y="4" width="62" height="72" rx="3" fill="none" stroke="#7dc242" stroke-width="5"/><path d="M35 4 V76 M4 30 H66" stroke="#7dc242" stroke-width="4"/><rect x="27" y="44" width="4" height="12" rx="2" fill="#7dc242"/><rect x="39" y="44" width="4" height="12" rx="2" fill="#7dc242"/></svg>
  <h3>ALTRA Windows</h3>
  <p>5 chamber noise reducing glazing with high temperature and noise insulation efficiency</p>
</div>
<div class="card" style="left:456px">
  <svg width="84" height="70" viewBox="0 0 84 70"><g fill="#7dc242"><rect x="2" y="2" width="24" height="18" rx="3"/><rect x="30" y="2" width="24" height="18" rx="3"/><rect x="58" y="2" width="24" height="18" rx="3"/><rect x="2" y="26" width="24" height="18" rx="3"/><rect x="30" y="26" width="24" height="18" rx="3"/><rect x="58" y="26" width="24" height="18" rx="3"/><rect x="2" y="50" width="24" height="18" rx="3"/><rect x="30" y="50" width="24" height="18" rx="3"/><rect x="58" y="50" width="24" height="18" rx="3"/></g></svg>
  <h3>Keramon bricks</h3>
  <p>Austrian Keramon Thermocell bricks with porous system and 25 cm thick outer walls</p>
</div>
<div class="card" style="left:768px">
  <svg width="50" height="76" viewBox="0 0 50 76"><path d="M25 4 a20 20 0 0 1 12 36 v12 h-24 v-12 a20 20 0 0 1 12 -36 z" fill="none" stroke="#7dc242" stroke-width="5"/><path d="M16 60 h18 M18 68 h14" stroke="#7dc242" stroke-width="5"/></svg>
  <h3>High Ceilings</h3>
  <p>2.70m high ceilings giving the light and space you need</p>
</div>
<div class="arrow" style="left:1078px;top:2609px"><svg width="12" height="18" viewBox="0 0 12 18"><path d="M3 2 L9 9 L3 16" fill="none" stroke="#555" stroke-width="2"/></svg></div>

<!-- location -->
<div class="map" role="img" aria-label="Map of North America with a pin on the West Coast"></div>
<div class="loc-card">
  <h2>LOCATION</h2>
  <p>Lorem ipsum dolor sit amet, consectetur adipiscing elit, sed do eiusmod tempor incididunt ut labore et dolore magna aliquis ipsum suspendisse ultrices gravids commodo viverra maecenas</p>
</div>

<!-- gallery -->
<h2 class="section-title" style="top:3434px">GALLERY</h2>
<p class="gal-sub">Sed ut perspiciatis unde omnis iste natus error sit voluptatem</p>
<div class="arrow" style="left:76px;top:3664px"><svg width="12" height="18" viewBox="0 0 12 18"><path d="M9 2 L3 9 L9 16" fill="none" stroke="#555" stroke-width="2"/></svg></div>
<div class="shot" style="left:145px;background:linear-gradient(180deg,#4a78b8,#8c4a36 45%,#5a3a2c)" role="img" aria-label="Red brick apartment block under blue sky">
  <span>April 2021</span><div class="btn">VIEW</div></div>
<div class="shot" style="left:457px;background:linear-gradient(180deg,#1f2a44,#6a5a4c 45%,#3a3028)" role="img" aria-label="Modern apartment block at dusk">
  <span>March 2021</span><div class="btn">VIEW</div></div>
<div class="shot" style="left:768px;background:linear-gradient(180deg,#1d2f5a,#5a6670 45%,#2a2e34)" role="img" aria-label="Apartment buildings at night">
  <span>March 2021</span><div class="btn">VIEW</div></div>
<div class="arrow" style="left:1078px;top:3664px"><svg width="12" height="18" viewBox="0 0 12 18"><path d="M3 2 L9 9 L3 16" fill="none" stroke="#555" stroke-width="2"/></svg></div>

<!-- contact -->
<footer class="contact">
  <svg class="abs" style="left:0;top:0" width="1200" height="696" viewBox="0 0 1200 696">
    <polygon points="0,278 416,12 600,145 780,12 1200,278 1200,696 0,696" fill="#1f1b1b"/>
    <polyline points="0,300 416,34 600,167 780,34 1200,300" fill="none" stroke="#7dc242" stroke-width="9"/>
  </svg>
  <h2>CONTACT</h2>
  <div class="col-title" style="left:193px;top:312px">ADDRESS</div>
  <div class="col-title" style="left:633px;top:312px">GET IN TOUCH</div>
  <div class="info" style="top:370px"><span class="c"><svg width="20" height="26" viewBox="0 0 20 26"><path d="M10 1 a9 9 0 0 1 9 9 c0 7 -9 15 -9 15 s-9 -8 -9 -15 a9 9 0 0 1 9 -9z" fill="#fff"/><circle cx="10" cy="10" r="3.5" fill="#7dc242"/></svg></span><span>213,Sed ut perspiciatis unde omnis iste<br>natus error sit voluptatem</span></div>
  <div class="info" style="top:439px"><span class="c"><svg width="22" height="22" viewBox="0 0 22 22"><path d="M5 1 l4 5 -2 3 c1 3 3 5 6 6 l3 -2 5 4 -2 4 c-9 0 -18 -9 -18 -18z" fill="#fff"/></svg></span><span>Tel:&nbsp; (555) 014-2270</span></div>
  <div class="info" style="top:506px"><span class="c"><svg width="24" height="18" viewBox="0 0 24 18"><rect x="1" y="1" width="22" height="16" fill="#fff"/><path d="M1 1 L12 10 L23 1" fill="none" stroke="#7dc242" stroke-width="2"/></svg></span><span>Email: info@pinehollow-homes.com</span></div>
  <div class="field" style="top:364px">Name</div>
  <div class="field" style="top:421px">Email Id</div>
  <div class="field" style="top:478px">Message</div>
  <div class="send">SEND</div>
  <div class="copy">Copyrights © 2021 Pinehollow.All Rights Reserved &nbsp;|&nbsp; Privacy Policy &nbsp;|&nbsp; Terms and conditions</div>
</footer>

</body>
</html>
```